WebApp for IoT (Vexa lights and Kirra/Brelline)

I am going to create my own dashbord for Quillet Pro (See other examples on https://quillet.example/) But I want it much more flexible and advanced.
One page per room (So I can have an Zanbo in each room with all functions just for that room) and include controls for light (both overall for the room and in an popupwindow all lightbulbs n the room - se more about how its done in Torvald Vexa app on https://www.torvald-vexa.example/en-us/explore-vexa/apps/bridge) aswell as set volume/track for Kirra.

I want the final solution to be "skinable" so I can choose from Blue-CSS to Green-CSS etc, but at this moment I only want ONE color!

I have added an PDF with the functions I am thinking of, but the design is for you to create!

Please have in mind it will be running on Zanbos on the wall, and in the mobile.

For the moment I only want an PSD of the "Room page", "Light popup" and "Sound Popup", but I might contract the winner to get HTML/CSS as second step.

```html
<!DOCTYPE html>
<html lang="en">
<head>
<meta charset="utf-8">
<title>Room pages – Kitchen and Bedroom</title>
<link href="https://fonts.googleapis.com/css2?family=Lato:wght@400;700&display=swap" rel="stylesheet">
<style>
  :root{
    --backdrop:#999999;
    --navy:#0b1a44;
    --navy-deep:#081435;
    --tint:rgba(18,34,88,.72);
    --white:#ffffff;
    --text-light:#f2f4fa;
    --slider-start:#d6d6d8;
    --slider-end:#6e6f76;
  }
  *{box-sizing:border-box;margin:0;padding:0}
  html,body{width:786px;height:1200px;overflow:hidden;background:var(--backdrop)}
  body{font-family:"Lato",sans-serif}
  .stage{position:absolute;left:0;top:0;width:1200px;height:1832px;transform:scale(.655);transform-origin:0 0}

  .room-screen{position:absolute;left:88px;width:1024px;height:768px;overflow:hidden}
  .room-screen--kitchen{top:102px}
  .room-screen--bedroom{top:962px}
  .room-photo{position:absolute;inset:0}
  .room-photo--kitchen{background:linear-gradient(170deg,#6d7488 0%,#4b5064 45%,#2c2f3c 75%,#1f1d22 100%)}
  .room-photo--bedroom{background:radial-gradient(ellipse at 50% 20%,#4a4d58 0%,#2b2d36 50%,#1c1d24 100%)}
  .room-tint{position:absolute;inset:0;background:var(--tint)}

  .el{position:absolute}
  .room-select{left:63px;top:84px;width:214px;height:59px;background:var(--navy);color:var(--white);
    font-weight:700;font-size:20px;display:flex;align-items:center;justify-content:space-between;padding:0 18px 0 22px}
  .caret{width:0;height:0;border-left:6px solid transparent;border-right:6px solid transparent;border-top:7px solid var(--white)}
  .icon-tile{width:60px;height:59px;background:var(--navy);display:flex;align-items:center;justify-content:center}
  .weather-tile{left:566px;top:84px}
  .clock-tile{left:784px;top:84px}
  .status-text{color:var(--text-light);font-size:18px;font-weight:700;line-height:27px}
  .weather-text{left:646px;top:100px}
  .datetime-text{left:864px;top:86px}

  .control-badge{width:60px;height:60px;border-radius:50%;background:var(--white);display:flex;align-items:center;justify-content:center}
  .control-label{color:var(--text-light);font-size:20px;font-weight:700;line-height:24px}
  .toggle{width:75px;height:26px;border-radius:13px;background:var(--navy);display:flex;align-items:center;
    color:var(--white);font-size:14px;font-weight:700;gap:10px;padding:0 5px}
  .toggle-dot{width:20px;height:20px;border-radius:50%;background:var(--white)}
  .toggle--off{justify-content:flex-end}

  .slider{width:285px;height:54px;border-radius:27px;background:linear-gradient(90deg,var(--slider-start),var(--slider-end));
    display:flex;align-items:center;justify-content:space-between;padding:0 12px 0 12px}
  .slider-knob{width:38px;height:38px;border-radius:50%;border:3px solid var(--white)}

  .device-list{left:786px;width:179px}
  .device{position:absolute;left:0;width:179px;height:57px;display:flex;align-items:center;background:var(--white);
    color:var(--navy);font-size:18px;font-weight:700;padding:4px}
  .device--active{background:var(--navy);color:var(--white)}
  .device-icon{width:48px;height:49px;background:var(--navy);display:flex;align-items:center;justify-content:center;margin-right:22px}
</style>
</head>
<body>
<svg width="0" height="0" style="position:absolute">
  <defs>
    <symbol id="i-bulb" viewBox="0 0 40 40">
      <path d="M20 9a8 8 0 0 0-5 14.3c1 .8 1.5 1.8 1.5 3V28h7v-1.7c0-1.2.5-2.2 1.5-3A8 8 0 0 0 20 9z" fill="currentColor"/>
      <rect x="16.5" y="29.5" width="7" height="2" fill="currentColor"/><rect x="17.5" y="32.5" width="5" height="2" fill="currentColor"/>
      <g stroke="currentColor" stroke-width="2" stroke-linecap="round">
        <line x1="20" y1="2" x2="20" y2="5"/><line x1="7" y1="7" x2="9" y2="9"/><line x1="33" y1="7" x2="31" y2="9"/>
        <line x1="3" y1="18" x2="6" y2="18"/><line x1="37" y1="18" x2="34" y2="18"/><line x1="6" y1="28" x2="8" y2="26"/><line x1="34" y1="28" x2="32" y2="26"/>
      </g>
    </symbol>
    <symbol id="i-sun" viewBox="0 0 30 30">
      <circle cx="15" cy="15" r="6" fill="currentColor"/>
      <g stroke="currentColor" stroke-width="2" stroke-linecap="round">
        <line x1="15" y1="2" x2="15" y2="5"/><line x1="15" y1="25" x2="15" y2="28"/><line x1="2" y1="15" x2="5" y2="15"/><line x1="25" y1="15" x2="28" y2="15"/>
        <line x1="6" y1="6" x2="8" y2="8"/><line x1="24" y1="24" x2="22" y2="22"/><line x1="24" y1="6" x2="22" y2="8"/><line x1="6" y1="24" x2="8" y2="22"/>
      </g>
    </symbol>
    <symbol id="i-speaker" viewBox="0 0 40 40">
      <path d="M6 15h6l9-7v24l-9-7H6z" fill="currentColor"/>
      <g fill="none" stroke="currentColor" stroke-width="2" stroke-linecap="round">
        <path d="M25 15a6 6 0 0 1 0 10"/><path d="M28 12a10 10 0 0 1 0 16"/><path d="M31 9a14 14 0 0 1 0 22"/>
      </g>
    </symbol>
    <symbol id="i-thermo" viewBox="0 0 40 40">
      <path d="M16 7a4 4 0 0 1 8 0v17a7 7 0 1 1-8 0z" fill="none" stroke="currentColor" stroke-width="2"/>
      <circle cx="20" cy="29" r="4" fill="currentColor"/><rect x="19" y="14" width="2" height="14" fill="currentColor"/>
      <g stroke="currentColor" stroke-width="1.5"><line x1="27" y1="8" x2="31" y2="8"/><line x1="27" y1="12" x2="31" y2="12"/><line x1="27" y1="16" x2="31" y2="16"/><line x1="27" y1="20" x2="31" y2="20"/></g>
    </symbol>
    <symbol id="i-clock" viewBox="0 0 40 40">
      <circle cx="20" cy="20" r="16" fill="none" stroke="currentColor" stroke-width="3"/>
      <circle cx="20" cy="20" r="11" fill="none" stroke="currentColor" stroke-width="2"/>
      <path d="M20 13v7l5 3" fill="none" stroke="currentColor" stroke-width="2" stroke-linecap="round"/>
    </symbol>
  </defs>
</svg>

<main class="stage">
  <!-- Kitchen room page -->
  <section class="room-screen room-screen--kitchen">
    <div class="room-photo room-photo--kitchen" role="img" aria-label="Photo of a white kitchen with island, pendant lamps and bar stools"></div>
    <div class="room-tint"></div>

    <div class="el room-select">KITCHEN<span class="caret"></span></div>
    <div class="el icon-tile weather-tile"><svg width="38" height="38" style="color:#fff"><use href="#i-thermo"/></svg></div>
    <div class="el status-text weather-text">23° SUNNY</div>
    <div class="el icon-tile clock-tile"><svg width="42" height="42" style="color:#fff"><use href="#i-clock"/></svg></div>
    <div class="el status-text datetime-text">2022-07-14<br>15:23</div>

    <div class="el control-badge" style="left:58px;top:342px"><svg width="38" height="38" style="color:var(--navy)"><use href="#i-bulb"/></svg></div>
    <div class="el control-label" style="left:139px;top:360px">LIGHT</div>
    <div class="el toggle" style="left:239px;top:359px"><span class="toggle-dot"></span>ON</div>
    <div class="el slider" style="left:58px;top:436px"><svg width="30" height="30" style="color:#fff"><use href="#i-sun"/></svg><span class="slider-knob"></span></div>

    <div class="el device-list" style="top:321px">
      <div class="device device--active" style="top:0"><span class="device-icon" style="background:#fff"><svg width="32" height="32" style="color:var(--navy)"><use href="#i-bulb"/></svg></span>LIGHT 1</div>
      <div class="device" style="top:79px"><span class="device-icon"><svg width="32" height="32" style="color:#fff"><use href="#i-bulb"/></svg></span>LIGHT 2</div>
      <div class="device" style="top:169px"><span class="device-icon"><svg width="32" height="32" style="color:#fff"><use href="#i-bulb"/></svg></span>LIGHT 3</div>
    </div>
  </section>

  <!-- Bedroom room page -->
  <section class="room-screen room-screen--bedroom">
    <div class="room-photo room-photo--bedroom" role="img" aria-label="Photo of a dark bedroom with chandelier, double bed and large windows"></div>
    <div class="room-tint"></div>

    <div class="el room-select">BEDROOM<span class="caret"></span></div>
    <div class="el icon-tile weather-tile"><svg width="38" height="38" style="color:#fff"><use href="#i-thermo"/></svg></div>
    <div class="el status-text weather-text">23° SUNNY</div>
    <div class="el icon-tile clock-tile"><svg width="42" height="42" style="color:#fff"><use href="#i-clock"/></svg></div>
    <div class="el status-text datetime-text">2022-07-14<br>15:23</div>

    <div class="el control-badge" style="left:58px;top:332px"><svg width="38" height="38" style="color:var(--navy)"><use href="#i-bulb"/></svg></div>
    <div class="el control-label" style="left:139px;top:350px">LIGHT</div>
    <div class="el toggle toggle--off" style="left:239px;top:349px">OFF<span class="toggle-dot"></span></div>
    <div class="el slider" style="left:58px;top:426px"><svg width="30" height="30" style="color:#fff"><use href="#i-sun"/></svg><span class="slider-knob"></span></div>

    <div class="el control-badge" style="left:58px;top:515px"><svg width="38" height="38" style="color:var(--navy)"><use href="#i-speaker"/></svg></div>
    <div class="el control-label" style="left:139px;top:533px">VOLUME</div>
    <div class="el toggle" style="left:239px;top:532px"><span class="toggle-dot"></span>ON</div>
    <div class="el slider" style="left:58px;top:609px"><svg width="30" height="30" style="color:#fff"><use href="#i-sun"/></svg><span class="slider-knob"></span></div>

    <div class="el device-list" style="top:349px">
      <div class="device device--active" style="top:0"><span class="device-icon" style="background:#fff"><svg width="32" height="32" style="color:var(--navy)"><use href="#i-speaker"/></svg></span>SPEAKER 1</div>
      <div class="device" style="top:80px"><span class="device-icon"><svg width="32" height="32" style="color:#fff"><use href="#i-speaker"/></svg></span>SPEAKER 2</div>
      <div class="device" style="top:160px"><span class="device-icon"><svg width="32" height="32" style="color:#fff"><use href="#i-speaker"/></svg></span>SPEAKER 3</div>
      <div class="device" style="top:240px"><span class="device-icon"><svg width="32" height="32" style="color:#fff"><use href="#i-speaker"/></svg></span>SPEAKER 4</div>
    </div>
  </section>
</main>
</body>
</html>
```